Boutique custom software development company needs new business card

Our nearly 20 year old custom software development company would like to better include the fact that we are now providing Bitcoin services. These new services are B2B include education (how to acquire and securely hold Bitcoin) and integrating Bitcoin payments into existing ecommerce sites or other existing systems. Please keep the card clean and simple. Attached is our current design and some other files. vextorial.com

Target Market(s)

businesses owners interested in long term relationship

Industry/Entity Type

Custom software development and Bitcoin

Contact Information for Business Card

Dale Parker, dale@vextorial.com, vextorial.com, (888) 555-VXTRL

Font styles to use
Other font styles liked:
• monospace

Requirements
Must have
• double-sided
Nice to have
• clean and simple
Should not have
• physical address

```html
<!DOCTYPE html>
<html lang="en">
<head>
<meta charset="utf-8">
<title>Vextorial Business Card</title>
<link rel="stylesheet" href="https://fonts.googleapis.com/css2?family=Montserrat:wght@400;500;700;800&display=swap">
<style>
  :root {
    --bg: #8a8a88;
    --paper: #ffffff;
    --brand-blue: #3a6bbf;
    --deep-blue: #1f55a8;
    --light-blue: #6f9ad6;
    --accent-orange: #f07a22;
    --ink-grey: #4a4a4a;
  }
  * { margin: 0; padding: 0; box-sizing: border-box; }
  html, body { width: 1200px; height: 801px; overflow: hidden; }
  body {
    background: var(--bg);
    font-family: "Montserrat", Arial, sans-serif;
    position: relative;
  }
  .card {
    position: absolute;
    top: 246px;
    width: 540px;
    height: 309px;
    border-radius: 2px;
    overflow: hidden;
  }
  .card--front { left: 40px; background: var(--paper); }
  .card--back { left: 620px; }

  .front-logo {
    position: absolute;
    left: 40px;
    top: 126px;
    width: 236px;
  }
  .brand-name {
    font-weight: 800;
    font-size: 34px;
    color: var(--brand-blue);
    letter-spacing: 0.5px;
    line-height: 1;
    text-transform: uppercase;
  }
  .brand-tagline {
    font-weight: 500;
    font-size: 11.5px;
    color: var(--brand-blue);
    margin-top: 6px;
    line-height: 1.35;
  }
  .brand-services {
    font-weight: 500;
    font-size: 11.5px;
    color: var(--accent-orange);
    line-height: 1.35;
  }
  .divider {
    position: absolute;
    left: 296px;
    top: 96px;
    width: 1px;
    height: 116px;
    background: var(--brand-blue);
    opacity: 0.7;
  }
  .contact {
    position: absolute;
    left: 318px;
    top: 104px;
  }
  .contact-name {
    font-weight: 700;
    font-size: 19px;
    color: var(--brand-blue);
    text-transform: uppercase;
    letter-spacing: 0.5px;
    margin-bottom: 10px;
  }
  .contact-list { list-style: none; }
  .contact-item {
    display: flex;
    align-items: center;
    gap: 8px;
    font-size: 13.5px;
    color: var(--ink-grey);
    line-height: 1.55;
  }
  .contact-icon { width: 11px; height: 11px; flex: none; }

  .back-pattern {
    position: absolute;
    inset: 0;
    background: linear-gradient(120deg, var(--deep-blue) 0%, var(--brand-blue) 55%, var(--light-blue) 100%);
  }
  .back-logo {
    position: absolute;
    right: 36px;
    bottom: 70px;
    text-align: left;
  }
  .back-logo .brand-name { color: var(--paper); font-size: 40px; }
  .back-logo .brand-tagline { color: var(--paper); font-size: 13.5px; }
  .back-logo .brand-services { color: var(--paper); font-size: 13.5px; opacity: 0.9; }
</style>
</head>
<body>
  <section class="card card--front" aria-label="Business card front">
    <div class="front-logo">
      <div class="brand-name">Vextorial</div>
      <div class="brand-tagline">developer of custom applications</div>
      <div class="brand-services">&amp; B2B bitcoin services</div>
    </div>
    <div class="divider"></div>
    <div class="contact">
      <div class="contact-name">Dale Parker</div>
      <ul class="contact-list">
        <li class="contact-item">
          <svg class="contact-icon" viewBox="0 0 12 12" aria-hidden="true"><path fill="var(--accent-orange)" d="M2.5 1h2l1 2.5-1.3 1a6 6 0 0 0 3.3 3.3l1-1.3L11 7.5v2a1.5 1.5 0 0 1-1.5 1.5A8.5 8.5 0 0 1 1 2.5 1.5 1.5 0 0 1 2.5 1z"/></svg>
          (888) 555-VXTRL
        </li>
        <li class="contact-item">
          <svg class="contact-icon" viewBox="0 0 12 12" aria-hidden="true"><rect x="0.5" y="2.5" width="11" height="7.5" fill="var(--accent-orange)"/><path d="M0.8 2.8 6 6.8l5.2-4" fill="none" stroke="#fff" stroke-width="1"/></svg>
          dale@vextorial.com
        </li>
        <li class="contact-item">
          <svg class="contact-icon" viewBox="0 0 12 12" aria-hidden="true"><circle cx="6" cy="6" r="5.5" fill="var(--accent-orange)"/><path d="M0.5 6h11M6 0.5c-2.5 3-2.5 8 0 11M6 0.5c2.5 3 2.5 8 0 11" fill="none" stroke="#fff" stroke-width="0.8"/></svg>
          www.vextorial.com
        </li>
      </ul>
    </div>
  </section>

  <section class="card card--back" aria-label="Business card back">
    <div class="back-pattern" role="img" aria-label="Repeating embossed brand-mark pattern in blue tones"></div>
    <div class="back-logo">
      <div class="brand-name">Vextorial</div>
      <div class="brand-tagline">developer of custom applications</div>
      <div class="brand-services">&amp; B2B bitcoin services</div>
    </div>
  </section>
</body>
</html>
```